Web design for financial services

A modern web design of financial services (brokerage firm)
Req.s and technology tags :
- Very mobile friendly.
- One paged with some inner pages.
- Animated sticky header .
- Member login area for e-trade.
- Support RTL language.
- HTML & CSS.

The logo will be Home link
• MPTR :
WHO WE ARE
Content :
i) Board of Directors
ii) Mission Statement
iii) Corporate Values
iv) Regulations
• Financial Services :
WHAT WE DO
Content:
i) Electronic trading
ii) Trading desk
iii) Institutional
iv) Investors Education
• News
• Market Tools
• Forms---- opens new page
• Careers---- opens new page
• Contact Us----opens new page

The website is :
http://www.mptr-doha-example.com/

The logo need some changes to be more modern and impressively , but with keeping same structure .

Some related websites :
https://www.lv-bourse.example/

financial market

Financial Service

Coded - Design and coding required

2 page

• same fonts of http://www.kwdholdings.example/

• - Very mobile friendly.
• - One paged with some inner pages.
• - Animated sticky header .
• - Member login area for e-trade.
• - Support RTL language.
• - HTML & CSS.
• Slider , some Qatari theme,
• i like the video inside the home page
• ex :http://www.kwdholdings.example/

```html
<!DOCTYPE html>
<html lang="en">
<head>
<meta charset="utf-8">
<title>MPTR – Market Data</title>
<link rel="stylesheet" href="https://fonts.googleapis.com/css2?family=Open+Sans:wght@400;600;700;800&display=swap">
<style>
:root{
  --brand:#9b2a28;
  --brand-dark:#7a1e1c;
  --ink:#222;
  --muted:#777;
  --line:#e2e2e2;
  --green:#5b9a2f;
  --footer:#000;
  --white:#fff;
}
*{box-sizing:border-box;margin:0;padding:0}
html,body{width:1200px;height:2356px;overflow:hidden}
body{font-family:"Open Sans",Arial,sans-serif;color:var(--ink);background:var(--white);position:relative}
.abs{position:absolute}

/* header */
.site-header{position:absolute;left:0;top:0;width:1200px;height:120px;background:var(--white)}
.brand{position:absolute;left:78px;top:34px;display:flex;align-items:center;gap:14px}
.brand-mark{width:44px;height:44px;border:7px solid var(--brand);border-radius:50%}
.brand-name{font-size:42px;font-weight:800;color:var(--ink);letter-spacing:-1px}
.top-actions{position:absolute;top:27px;right:76px;display:flex;gap:10px}
.btn-etrade{height:27px;padding:0 10px;background:var(--brand);color:var(--white);font-size:10px;font-weight:700;display:flex;align-items:center;gap:6px;border-radius:2px}
.btn-etrade span.ico{width:10px;height:10px;border:1.5px solid var(--white)}
.btn-lang{height:27px;padding:0 10px;border:1px solid #999;font-size:9px;font-weight:600;display:flex;align-items:center;gap:6px;border-radius:2px}
.btn-lang .flag{width:14px;height:9px;background:#2b3f8c}
.main-nav{position:absolute;top:82px;right:76px;display:flex;gap:30px;font-size:12px;font-weight:700;text-transform:uppercase}
.main-nav .active{color:var(--brand)}

/* hero */
.hero{position:absolute;left:0;top:120px;width:1200px;height:550px;background:linear-gradient(120deg,#3a2a22 0%,#6a4b38 35%,#8a7a70 55%,#2e2a2a 100%)}
.hero-title{position:absolute;top:300px;width:1200px;text-align:center;color:var(--white);font-size:62px;font-weight:700;letter-spacing:1px}
.hero-cut{position:absolute;left:0;top:500px}

/* intro */
.section-label{position:absolute;left:160px;top:702px;font-size:15px;font-weight:700;color:var(--brand);text-transform:uppercase}
.section-label::after{content:"";position:absolute;left:0;top:32px;width:46px;height:4px;background:var(--ink)}
.intro-divider{position:absolute;left:340px;top:700px;width:1px;height:170px;background:#d6d6d6}
.intro-text{position:absolute;left:382px;top:700px;width:658px;font-size:11.2px;line-height:21.8px;color:#333}

/* status bar */
.status-bar{position:absolute;left:162px;top:943px;width:876px;height:88px;border:3px solid #e6e6e6;display:flex;align-items:center}
.status-cell{height:100%;display:flex;align-items:center;border-right:1px solid var(--line);padding:0 10px;gap:10px}
.status-cell:last-child{border-right:0}
.status-cell small{display:block;font-size:11px;color:var(--ink)}
.status-cell b{display:block;font-size:15px;font-weight:600}
.status-cell .cap{font-size:11px;font-weight:600;text-transform:uppercase}
.status-cell .sub{font-size:10px;color:var(--brand);text-transform:uppercase;font-weight:600}
.ring{width:34px;height:34px;border:5px solid var(--brand);border-radius:50%;position:relative}
.up{color:var(--green)}

/* headings */
.block-title{position:absolute;top:1084px;font-size:20px;font-weight:700;color:var(--brand);text-transform:uppercase}

/* chart */
.chart-box{position:absolute;left:160px;top:1172px;width:414px;height:381px;border:1px solid var(--line)}
.chart-meta{position:absolute;left:16px;top:12px;font-size:10px;color:var(--muted)}
.range-tabs{position:absolute;left:16px;top:42px;width:378px;display:flex;justify-content:space-between;font-size:10.5px;font-weight:600;border-bottom:2px solid #ddd;padding:0 8px 10px}
.range-tabs .on{color:var(--brand);position:relative}
.range-tabs .on::after{content:"";position:absolute;left:-6px;right:-6px;bottom:-12px;height:2px;background:var(--brand)}
.prev-close{position:absolute;left:16px;top:92px;font-size:10px;color:#444}

/* movers */
.movers-tabs{position:absolute;left:627px;top:1138px;width:412px;display:flex;justify-content:space-between;font-size:13px;font-weight:700;text-transform:uppercase;padding-right:20px}
.movers-table{position:absolute;left:623px;top:1172px;width:416px;height:381px;border:1px solid var(--line);border-top:2px solid var(--brand);border-collapse:collapse;font-size:11px}
.movers-table th{height:29px;font-size:9.5px;font-weight:400;color:var(--muted)}
.movers-table td{height:38px;border-top:1px solid var(--line)}
.movers-table td:first-child{padding-left:17px;color:var(--brand);font-weight:700;width:170px}
.movers-table td:nth-child(2){width:130px}
.movers-table td:last-child{text-align:center;padding-right:30px}
.movers-table tr.hl td{background:#e4e4e4}

/* skyline */
.skyline{position:absolute;left:0;top:1775px;width:1200px;height:327px;background:linear-gradient(180deg,rgba(255,255,255,0) 0%,#e8c3c0 30%,#b4524c 80%,#8e2f2b 100%);clip-path:polygon(0 72%,3% 72%,7% 38%,13% 38%,17% 20%,25% 20%,29% 0,33% 20%,38% 20%,41% 28%,47% 8%,52% 30%,57% 15%,63% 30%,69% 32%,74% 42%,80% 40%,85% 48%,90% 30%,96% 38%,100% 44%,100% 100%,0 100%)}

/* footer */
.site-footer{position:absolute;left:0;top:2102px;width:1200px;height:254px;background:var(--footer);color:var(--white);text-align:center}
.footer-brand{position:absolute;top:52px;width:1200px;display:flex;justify-content:center;align-items:center;gap:10px}
.footer-brand .brand-mark{width:32px;height:32px;border:5px solid var(--white)}
.footer-brand .brand-name{font-size:28px;color:var(--white)}
.footer-nav{position:absolute;top:126px;width:1200px;font-size:14px;font-weight:700;word-spacing:2px}
.footer-nav span{margin:0 10px}
.copyright{position:absolute;top:160px;width:1200px;font-size:10.5px}
.socials{position:absolute;top:193px;width:1200px;display:flex;justify-content:center;gap:8px}
.socials i{width:26px;height:26px;border:1.5px solid var(--white);border-radius:50%}
</style>
</head>
<body>

<header class="site-header">
  <div class="brand"><div class="brand-mark"></div><div class="brand-name">MPTR</div></div>
  <div class="top-actions">
    <div class="btn-etrade"><span class="ico"></span>MPTR E-TRADE</div>
    <div class="btn-lang"><span class="flag"></span>ENGLISH <span>&#9662;</span></div>
  </div>
  <nav class="main-nav">
    <span>MPTR</span><span>Financial Service</span><span>News</span><span class="active">Market Tool</span><span>Forms</span><span>Careers</span><span>Contact Us</span>
  </nav>
</header>

<section class="hero" role="img" aria-label="Photo of a person reviewing printed financial charts beside a laptop">
  <h1 class="hero-title" style="top:180px">MARKET DATA</h1>
  <svg class="hero-cut" width="1200" height="50" viewBox="0 0 1200 50" preserveAspectRatio="none" style="top:400px;height:150px">
    <polygon points="0,74 372,2 1200,148 1200,150 0,150" fill="#fff" transform="scale(1,0.333)"/>
  </svg>
</section>
<svg class="abs" style="left:0;top:520px" width="1200" height="152"><polygon points="0,75 372,2 1200,148 1200,152 0,152" fill="#fff"/></svg>

<section>
  <h2 class="section-label">Market Data</h2>
  <div class="intro-divider"></div>
  <p class="intro-text">Sed ut perspiciloatis unde omnis iste natus err or sit voluptat em accusantium dolore mque laudlorantium, totam remape riam, eaque ipsa quae ab illo inventore veritatis et quasi arc hite locto beatae vitae dictasnt explic abo enim ilorepsam vol uptatemloia voluptas sit aspe rnatur aut odit auhite cto bea tae vitae lodictasnt explic abo enim ilorepsam vol uptateloia voluptas sit aspe rnatur aut odit ahite cto beatae vitae dictst explic abo enim ilorepsam vol uptatemloia voluptas sit aspe rnatur aut odit auhite cto bea taipsa quae ab illo inventore veritatis et quasi arc hite locto beatae vitae dictasnt explic abo enim ilorepsam vol uptatemloia voluptas sit aspe rnatur aut odit auhite cto bea tae vitae lodictasnt explic abo enim ilorepsam vol uptateloia voluptas sit aspe rnatur aut odit ahite cto beatae vitae dictst explic abo enim ilorepsam vol uptatemloia voluptas sit aspe rnatur aut odit auhite cto bea taeipsa quae.</p>
</section>

<div class="status-bar">
  <div class="status-cell" style="width:152px"><div class="ring"></div><div><div class="cap">Market Status</div><div class="sub">Post Trading</div></div></div>
  <div class="status-cell" style="width:116px"><svg width="28" height="20"><polyline points="2,18 9,9 15,13 26,3" fill="none" stroke="#aaa" stroke-width="2"/></svg><div><b>20,046.60</b><small>Index</small></div></div>
  <div class="status-cell" style="width:132px"><div><b class="up">&#9650; 20.00(+0.14%)</b><small style="color:#999">Change</small></div></div>
  <div class="status-cell" style="width:70px"><div><b style="font-weight:400;font-size:14px">10,000</b><small>Trades</small></div></div>
  <div class="status-cell" style="width:66px"><div><b style="font-weight:400;font-size:14px">15,130</b><small style="color:#999">Volume</small></div></div>
  <div class="status-cell" style="width:128px"><div><b style="font-weight:400;font-size:14px">1,524,248,539.00</b><small>Value</small></div></div>
  <div class="status-cell" style="flex:1;padding-left:16px"><div class="ring" style="width:32px;height:32px;border-width:4px"></div><div><div class="cap">Last Updated</div><div class="sub">Feb 08, 2017 10:55:27 PM</div></div></div>
</div>

<h2 class="block-title" style="left:160px">Index Chart</h2>
<h2 class="block-title" style="left:623px">Market Movers</h2>

<div class="chart-box">
  <div class="chart-meta">MKT 500 | 4:40 Pm EST 02/13/2017</div>
  <div class="range-tabs"><span class="on">1D</span><span>5D</span><span>1M</span><span>3M</span><span>6M</span><span>1Y</span><span>5Y</span><span>YYD</span></div>
  <div class="prev-close">Previous Close: 1900.60</div>
  <svg class="abs" style="left:0;top:86px" width="414" height="295">
    <defs><linearGradient id="areaFill" x1="0" y1="0" x2="0" y2="1"><stop offset="0" stop-color="#9b2a28"/><stop offset="0.75" stop-color="#9b2a28" stop-opacity="0"/></linearGradient></defs>
    <g stroke="#eee" stroke-width="1"><line x1="16" y1="56" x2="340" y2="56"/><line x1="16" y1="96" x2="340" y2="96"/><line x1="16" y1="136" x2="340" y2="136"/><line x1="16" y1="176" x2="340" y2="176"/></g>
    <polygon points="16,112 160,26 330,26 330,260 16,260" fill="url(#areaFill)"/>
    <polyline points="16,112 160,26 330,26" fill="none" stroke="#8e2523" stroke-width="2"/>
    <rect x="338" y="16" width="60" height="20" fill="#9b2a28"/>
    <text x="368" y="30" font-size="10" fill="#fff" text-anchor="middle" font-family="Open Sans,sans-serif">19459.15</text>
    <g font-size="10" fill="#444" font-family="Open Sans,sans-serif"><text x="345" y="70">18925.00</text><text x="345" y="110">18900.00</text><text x="345" y="150">18875.00</text><text x="345" y="190">18850.00</text></g>
  </svg>
</div>

<div class="movers-tabs"><span>Top Gainers</span><span>Top Decliners</span><span>Top Active</span></div>
<table class="movers-table">
  <tr><th></th><th style="text-align:left">LAST</th><th style="padding-right:30px">%CHG</th></tr>
  <tr class="hl"><td>MKT 500</td><td>2328.00</td><td class="up">0.52%</td></tr>
  <tr><td>TECHCOMP</td><td>2328.00</td><td class="up">0.52%</td></tr>
  <tr><td>TECHCOMP</td><td>2328.00</td><td class="up">0.52%</td></tr>
  <tr><td>IND 30</td><td>2328.00</td><td class="up">0.52%</td></tr>
  <tr><td>* LDN 100</td><td>2328.00</td><td class="up">0.52%</td></tr>
  <tr><td>* TKY 225</td><td>2328.00</td><td>0%</td></tr>
  <tr><td>* HKG 50</td><td>2328.00</td><td>0%</td></tr>
  <tr><td>* VOLX</td><td>2328.00</td><td class="up">0.52%</td></tr>
  <tr><td>* FRK 40</td><td>2328.00</td><td class="up">0.52%</td></tr>
</table>

<div class="skyline" role="img" aria-label="Illustrated Doha city skyline in red tones"></div>

<footer class="site-footer">
  <div class="footer-brand"><div class="brand-mark"></div><div class="brand-name">MPTR</div></div>
  <div class="footer-nav">MPTR<span>|</span>FINACIAL SERVICE<span>|</span>NEWS<span>|</span>MARKET TOOL<span>|</span>CAREERS<span>|</span>CONTACT US</div>
  <div class="copyright">©2017. All Rights Reserved | MPTR Doha | Copyright, Legal and Privacy Statement.Disclaimers and Legal Information</div>
  <div class="socials"><i></i><i></i><i></i><i></i><i></i></div>
</footer>

</body>
</html>
```